creative brochure for lumawell advisory an innovative consulting company!

Im looking for a brochure to be designed. I am happy for the designer to be creative with it. Please use the colors from my logo and you can look at my website www.lumawelladvisory.example to get a feel. I will provide all the wording. Its aimed at small business owners and i want it to give off the vibe of professional and experienced.
The text logo and a photo of me is attached. Please edit the photo of me to make me look slimmer!
If you want to change text because you can make it sound better please go ahead. use my website to see if there is any other information in it that would make the brochure better or more credible/convincing.
I am open to ideas, lay out and how many pages it should be or if it should be double sided. I need one i can email and one i can print. Maybe use the sentence "Turn your business around now as the point which jumps out the most".
Updates

I have just uploaded a bigger version of the photo as requested. Please photoshop it to make me look thinner and perhaps crop it at the waist. Thanks

Hi everyone, great work so far. Im liking the designs. Maybe just a bit less color. you could use grey i guess or other plain colors. Im not a fan of the orange in my logo so just use it minimally in the next ones. Still considering the ones submitted though.

Hi everyone, please remove the words, jumps out as the main point and just have, turn your business around now.

Thanks

Could you please also include this email address in the contact details

maren.toovey@lumawelladvisory.example

Please change the words Turn your business around too unlock your business potential now.

Target Market(s)

Small business in australia

Industry/Entity Type

Small Business

Requirements
Must have
• as above, all that i have provided in the files must be used as a minimum
Nice to have
• great creative use of my brand colors
Should not have
• i dont want it to look to young or too over the top. I dont want any new colors.

```html
<!DOCTYPE html>
<html lang="en">
<head>
<meta charset="utf-8">
<title>lumawell advisory brochure</title>
<link rel="stylesheet" href="https://fonts.googleapis.com/css2?family=Arimo:wght@400;700&family=Archivo+Black&display=swap">
<style>
  :root {
    --purple-deep: #2f2650;
    --purple-mid: #6c628f;
    --purple-soft: #b9b3cc;
    --purple-mist: #d9d6e3;
    --orange-deep: #d4542a;
    --orange-bright: #f29a3a;
    --band-grey: #e7e7e9;
    --ink: #1d1a24;
    --ink-soft: #2a2a2a;
    --white: #ffffff;
  }
  * { margin: 0; padding: 0; box-sizing: border-box; }
  html, body { width: 1200px; height: 858px; overflow: hidden; background: var(--white); }
  .brochure { position: relative; width: 1200px; height: 858px; overflow: hidden; }

  .back-panel {
    position: absolute; left: 0; top: 0; width: 600px; height: 858px;
    background: linear-gradient(160deg, var(--purple-deep) 0%, var(--purple-mid) 45%, var(--purple-soft) 80%, var(--purple-mist) 100%);
    overflow: hidden;
  }
  .back-portrait {
    position: absolute; left: 40px; top: 70px; width: 520px; height: 790px;
    border-radius: 220px 220px 20px 20px;
    background: radial-gradient(ellipse at 50% 30%, rgba(235,225,235,0.3) 0%, rgba(120,110,150,0.22) 45%, rgba(60,50,90,0.12) 100%);
  }
  .contact-band {
    position: absolute; left: 0; top: 530px; width: 600px; height: 126px;
    background: var(--band-grey);
    display: flex; flex-direction: column; justify-content: center; align-items: center;
    font-family: "Arimo", Arial, sans-serif; font-size: 19px; line-height: 24.5px; color: var(--ink-soft);
    text-align: center;
  }

  .front-panel { position: absolute; left: 600px; top: 0; width: 600px; height: 858px; overflow: hidden; }
  .front-art { position: absolute; inset: 0; }
  .front-portrait {
    position: absolute; left: 18px; top: 378px; width: 294px; height: 396px;
    border-radius: 120px 120px 6px 6px;
    background: linear-gradient(180deg, #d9bf84 0%, #c9a98a 28%, #2b2b33 52%, #151519 100%);
  }

  .headline {
    position: absolute; left: 634px; top: 92px;
    transform: rotate(-6deg); transform-origin: left top;
    font-family: "Archivo Black", "Arimo", sans-serif; font-weight: 400; color: var(--ink);
    line-height: 1.08; white-space: nowrap;
  }
  .headline-top { display: block; font-size: 25px; letter-spacing: 0.6px; }
  .headline-main { display: block; font-size: 34px; letter-spacing: 0.4px; }

  .brand-name {
    position: absolute; left: 842px; top: 348px;
    display: flex; align-items: center; gap: 12px; white-space: nowrap;
    font-family: "Arimo", Arial, sans-serif; font-weight: 700; font-size: 31px; color: var(--ink);
    letter-spacing: -0.3px;
  }
  .brand-dot { width: 26px; height: 26px; border-radius: 50%; background: var(--orange-deep); }
</style>
</head>
<body>
<main class="brochure">
  <section class="back-panel">
    <div class="back-portrait" role="img" aria-label="Faded portrait of the consultant in a dark business suit"></div>
    <div class="contact-band">
      <p>www.lumawelladvisory.example</p>
      <p>ph : 95550148</p>
      <p>m : 0400555917</p>
      <p>e : maren.toovey@lumawelladvisory.example</p>
    </div>
  </section>

  <section class="front-panel">
    <svg class="front-art" width="600" height="858" viewBox="0 0 600 858" aria-hidden="true">
      <defs>
        <linearGradient id="face-purple" x1="0" y1="0" x2="1" y2="1">
          <stop offset="0" stop-color="#3a2f5e"/>
          <stop offset="0.5" stop-color="#7a6f9c"/>
          <stop offset="1" stop-color="#d8d4e4"/>
        </linearGradient>
        <linearGradient id="band-orange" x1="0" y1="0" x2="1" y2="0">
          <stop offset="0" stop-color="#d4542a"/>
          <stop offset="0.6" stop-color="#f29a3a"/>
          <stop offset="1" stop-color="#e0682c"/>
        </linearGradient>
      </defs>
      <rect class="panel-field" width="600" height="858" fill="url(#face-purple)"/>
      <polygon class="top-band" points="0,0 600,0 600,135 0,217" fill="url(#band-orange)"/>
      <path class="top-curve" d="M490 0 Q570 60 600 130 L600 0 Z" fill="#c44a22" opacity="0.5"/>
      <polygon class="top-rule" points="0,217 600,135 600,146 0,229" fill="#ffffff"/>
      <polygon class="bottom-rule" points="0,779 600,715 600,858 0,858" fill="#ffffff"/>
      <polygon class="bottom-band" points="0,797 600,732 600,858 0,858" fill="url(#band-orange)"/>
    </svg>
    <div class="front-portrait" role="img" aria-label="Portrait of the consultant with arms crossed, wearing a black blazer and white shirt"></div>
  </section>

  <h1 class="headline">
    <span class="headline-top">UNLOCK YOUR BUSINESS</span>
    <span class="headline-main">POTENTIAL NOW!!!</span>
  </h1>

  <div class="brand-name">
    <span class="brand-dot"></span>
    <span>lumawell advisory</span>
  </div>
</main>
</body>
</html>
```